Hair salon Business Card

Beauty Salon
I would like to see designs using sky blue and a soft orange. Mainly I would like my name ( Velvet Strand Salon ) used as the design

Industry/Entity Type

Business

Contact Information for Business Card

Velvet Strand Salon
318 E Maple Hyw #14
Brightwater, Ca 91850
909 555-2716

```html
<!DOCTYPE html>
<html lang="en">
<head>
<meta charset="utf-8">
<title>Velvet Strand Salon – Business Card</title>
<link rel="stylesheet" href="https://fonts.googleapis.com/css2?family=Cabin:wght@400&display=swap">
<style>
  :root {
    --backdrop: #1c1c1c;
    --card-white: #ffffff;
    --brand-blue: #215fb0;
    --brand-blue-deep: #1b4f95;
    --soft-orange: #d2822a;
    --ink: #1a1a1a;
  }
  * { margin: 0; padding: 0; box-sizing: border-box; }
  html, body {
    width: 1200px;
    height: 900px;
    overflow: hidden;
    background: var(--backdrop);
    font-family: "Cabin", "Helvetica Neue", Arial, sans-serif;
  }
  .canvas {
    position: relative;
    width: 1200px;
    height: 900px;
  }
  .card {
    position: absolute;
    top: 170px;
    width: 347px;
    height: 561px;
  }
  .card-front {
    left: 259px;
    background: var(--card-white);
  }
  .card-back {
    left: 631px;
    background: var(--brand-blue);
    display: flex;
    align-items: center;
    justify-content: center;
  }
  .accent-bar {
    position: absolute;
    left: 102px;
    width: 143px;
    height: 29px;
    background: var(--brand-blue);
  }
  .accent-bar-top { top: 0; }
  .accent-bar-bottom { bottom: 0; }

  .brand {
    position: absolute;
    top: 184px;
    left: 0;
    width: 100%;
    height: 40px;
    display: flex;
    align-items: center;
    justify-content: center;
    gap: 12px;
  }
  .brand-name {
    font-size: 30px;
    line-height: 40px;
    font-weight: 400;
    color: var(--brand-blue);
    white-space: nowrap;
  }
  .brand-dot {
    flex: none;
    width: 22px;
    height: 22px;
    border-radius: 50%;
    background: var(--soft-orange);
  }

  .contact {
    position: absolute;
    top: 327px;
    left: 0;
    width: 100%;
    text-align: center;
  }
  .contact-phone {
    display: flex;
    align-items: center;
    justify-content: center;
    gap: 8px;
    font-size: 17px;
    line-height: 22px;
    color: var(--soft-orange);
  }
  .contact-phone svg { width: 14px; height: 14px; fill: var(--brand-blue); }
  .contact-address {
    margin-top: 16px;
    font-size: 15px;
    line-height: 20px;
    color: var(--ink);
    font-style: normal;
  }

  .back-name {
    font-size: 30px;
    font-weight: 400;
    color: var(--brand-blue-deep);
    white-space: nowrap;
  }
</style>
</head>
<body>
<main class="canvas">
  <section class="card card-front" aria-label="Business card front">
    <div class="accent-bar accent-bar-top"></div>

    <div class="brand">
      <span class="brand-name">Velvet Strand Salon</span>
      <span class="brand-dot" aria-hidden="true"></span>
    </div>

    <div class="contact">
      <p class="contact-phone">
        <svg viewBox="0 0 24 24" aria-hidden="true">
          <path d="M6.6 10.8a15.1 15.1 0 0 0 6.6 6.6l2.2-2.2a1 1 0 0 1 1-.25 11.4 11.4 0 0 0 3.6.57 1 1 0 0 1 1 1V20a1 1 0 0 1-1 1A17 17 0 0 1 3 4a1 1 0 0 1 1-1h3.5a1 1 0 0 1 1 1c0 1.25.2 2.45.57 3.57a1 1 0 0 1-.25 1z"/>
        </svg>
        <span>909 555-2716</span>
      </p>
      <address class="contact-address">
        318 E Maple Hyw #14<br>
        Brightwater, Ca 91850
      </address>
    </div>

    <div class="accent-bar accent-bar-bottom"></div>
  </section>

  <section class="card card-back" aria-label="Business card back">
    <span class="back-name">Velvet Strand Salon</span>
  </section>
</main>
</body>
</html>
```